Zeltrova - Clever Automation

We are a software house for Audio Visual Systems integration/automation and home automation. we develop innovative software to automate a variety of devices mainly related to audio visuals and we design touch panel user interfaces to control these systems.

We would like to see designs that stick to our colours and theme, which you can find on our webpage www.zeltrova.com.au

The final design should communicate touch panels, innovation, software and automation.

Industry/Entity Type

Software

Requirements
Must have
• The business card must show the following information:
Name example : Derek Thalwin
Qualification example: B Eng ICT(CompSys) Dip EngPrac
Title example : Control Systems Programmer
Mobile Phone, Company phone, Email address ,Company website

```html
<!DOCTYPE html>
<html lang="en">
<head>
<meta charset="utf-8">
<title>Zeltrova – Business Card</title>
<link href="https://fonts.googleapis.com/css2?family=Mulish:wght@400;700&display=swap" rel="stylesheet">
<style>
  :root {
    --bg: #d9d9d9;
    --card: #ffffff;
    --brand-green: #3aa66a;
    --brand-blue: #2f7fc1;
    --ink: #4a4a4a;
    --ink-soft: #6a6a6a;
    --shadow: rgba(0, 0, 0, 0.22);
  }
  * { margin: 0; padding: 0; box-sizing: border-box; }
  html, body { width: 1200px; height: 871px; overflow: hidden; }
  body {
    background: var(--bg);
    font-family: "Mulish", sans-serif;
    position: relative;
  }
  .card {
    position: absolute;
    width: 560px;
    height: 320px;
    background: var(--card);
    box-shadow: 0 14px 30px var(--shadow);
  }
  .card--front { left: 80px; top: 120px; }
  .card--back  { left: 560px; top: 440px; }

  .brand {
    display: flex;
    align-items: center;
    gap: 14px;
  }
  .brand__square {
    width: 52px; height: 52px;
    background: var(--brand-blue);
    border-radius: 6px;
    flex: none;
  }
  .brand__text { display: flex; flex-direction: column; }
  .brand__name {
    font-size: 46px;
    font-weight: 700;
    color: var(--brand-green);
    line-height: 1;
    letter-spacing: -0.5px;
  }
  .brand__tagline {
    font-size: 11px;
    font-weight: 700;
    color: var(--ink);
    margin-top: 3px;
    align-self: flex-end;
  }
  .card--front .brand {
    position: absolute;
    left: 50%; top: 50%;
    transform: translate(-50%, -50%);
  }

  .card--back .brand { position: absolute; left: 30px; top: 34px; }
  .contact {
    position: absolute;
    left: 36px; top: 150px;
  }
  .contact__name {
    font-size: 20px;
    font-weight: 700;
    letter-spacing: 1.5px;
    color: var(--ink);
    margin-left: 34px;
  }
  .contact__qual { font-size: 13px; font-weight: 400; letter-spacing: 0.5px; }
  .contact__title {
    font-size: 14px;
    font-weight: 700;
    letter-spacing: 1px;
    color: var(--brand-green);
    margin: 2px 0 16px 34px;
  }
  .contact__list { list-style: none; }
  .contact__item {
    display: flex;
    align-items: center;
    gap: 12px;
    font-size: 13px;
    color: var(--ink-soft);
    margin-bottom: 9px;
  }
  .contact__icon { width: 14px; height: 14px; fill: var(--brand-green); flex: none; }
  .contact__web {
    font-size: 14px;
    color: var(--brand-blue);
    margin-top: 4px;
  }
  .contact__web span { color: var(--brand-green); }
</style>
</head>
<body>
  <section class="card card--front" aria-label="Business card front">
    <div class="brand">
      <div class="brand__square"></div>
      <div class="brand__text">
        <span class="brand__name">Zeltrova</span>
        <span class="brand__tagline">Clever Automation</span>
      </div>
    </div>
  </section>

  <section class="card card--back" aria-label="Business card back">
    <div class="brand">
      <div class="brand__square"></div>
      <div class="brand__text">
        <span class="brand__name">Zeltrova</span>
        <span class="brand__tagline">Clever Automation</span>
      </div>
    </div>

    <div class="contact">
      <p class="contact__name">Derek Thalwin, <span class="contact__qual">B Eng ICT</span></p>
      <p class="contact__title">Control Systems Programmer</p>
      <ul class="contact__list">
        <li class="contact__item">
          <svg class="contact__icon" viewBox="0 0 16 16" aria-hidden="true"><path d="M1 6c0-2 3-4 7-4s7 2 7 4v1h-4V5H5v2H1z"/><rect x="3" y="8" width="10" height="6" rx="1.5"/></svg>
          1.800.555.0142
        </li>
        <li class="contact__item">
          <svg class="contact__icon" viewBox="0 0 16 16" aria-hidden="true"><path d="M5 1h6a1 1 0 0 1 1 1v12a1 1 0 0 1-1 1H5a1 1 0 0 1-1-1V2a1 1 0 0 1 1-1zm1 2v8h4V3z"/></svg>
          604.555.0187
        </li>
        <li class="contact__item">
          <svg class="contact__icon" viewBox="0 0 16 16" aria-hidden="true"><path d="M1 3h14v10H1zm1.5 1.5L8 9l5.5-4.5z" fill-rule="evenodd"/></svg>
          derek@zeltrova.ca
        </li>
      </ul>
      <p class="contact__web">www.<span>zeltrova</span>.ca</p>
    </div>
  </section>
</body>
</html>
```